Modern Business Card for Larkwell 2018

Our company assumes the best about people. We are creating an online community of entrepreneurs and business leaders who struggle with marketing their business online.

This business card should POP! We recently got a new logo and are launching a new website next month, so our business cards should make a statement that feels:
-Fresh
-Smart
-Trustworthy
-Fun

Target Market(s)

small business owners, entrepreneurs

Industry/Entity Type

Digital Marketing

Contact Information for Business Card

Dimensions: 3.5" x 2"

Font styles to use
Sans Serif

Colors
f37122
ffffff

Requirements
Must have
• We need a business card with a modern, bold design. We will use one side of the card as a lead-generation offer, so text on one side will need to fit up to 140 characters. The business card should stick to our core colors (orange, black, and white).
Nice to have
• We think a vertical "portrait" design could be interesting.
Should not have
• Should not look like a traditional business card. The round icon should stand out from a distance.

```html
<!DOCTYPE html>
<html lang="en">
<head>
<meta charset="UTF-8">
<title>Larkwell Business Card</title>
<link href="https://fonts.googleapis.com/css2?family=Roboto:wght@400;500;900&family=Roboto+Condensed:wght@400;500&display=swap" rel="stylesheet">
<style>
  :root {
    --orange: #f37122;
    --orange-deep: #c9501a;
    --white: #ffffff;
    --ink: #2b2b2b;
    --rule: #8a8a8a;
    --brand-light: #c9c4c0;
    --stage: #3a3a3a;
  }
  * { margin: 0; padding: 0; box-sizing: border-box; }
  html, body { width: 1200px; height: 900px; overflow: hidden; }
  body {
    background: var(--stage);
    font-family: "Roboto", sans-serif;
    position: relative;
  }
  .card {
    position: absolute;
    left: 250px;
    width: 700px;
    height: 400px;
    border-radius: 26px;
    overflow: hidden;
  }
  /* Front */
  .card-front {
    top: 30px;
    background: linear-gradient(160deg, #e9e9e9 0%, var(--white) 55%);
  }
  .holder-name {
    position: absolute; left: 48px; top: 56px;
    color: var(--orange); font-size: 34px; font-weight: 500; letter-spacing: 1px;
  }
  .holder-title {
    position: absolute; left: 48px; top: 98px;
    color: var(--ink); font-size: 19px; letter-spacing: 0.5px;
  }
  .front-rule {
    position: absolute; left: 48px; right: 40px; top: 140px;
    height: 2px; background: var(--rule);
  }
  .contact-list {
    position: absolute; left: 48px; top: 166px;
    list-style: none; color: var(--ink); font-size: 19px; line-height: 1.45; letter-spacing: 0.4px;
  }
  .contact-list li { display: flex; align-items: center; gap: 10px; }
  .contact-list .addr { padding-left: 0; }
  .contact-list svg { width: 14px; height: 14px; flex: none; }
  .accent { color: var(--orange); }
  .front-brand {
    position: absolute; right: 48px; bottom: 80px;
    display: flex; align-items: center; gap: 14px;
  }
  .brand-dot { width: 38px; height: 38px; border-radius: 50%; background: var(--orange); }
  .brand-name {
    font-family: "Roboto", sans-serif; font-weight: 900; font-size: 48px;
    letter-spacing: 1px; color: var(--ink);
  }
  /* Back */
  .card-back {
    top: 470px;
    background: linear-gradient(135deg, var(--orange) 0%, var(--orange-deep) 100%);
  }
  .map-pattern {
    position: absolute; left: 60px; top: 30px; width: 580px; height: 300px;
    border-radius: 40px;
    background: radial-gradient(ellipse at center, rgba(255,255,255,0.10), rgba(255,255,255,0) 70%);
  }
  .back-brand {
    position: absolute; left: 0; right: 0; top: 70px;
    display: flex; flex-direction: column; align-items: center; gap: 14px;
  }
  .back-brand .brand-dot { width: 64px; height: 64px; background: var(--brand-light); }
  .back-brand .brand-name { color: var(--brand-light); font-size: 78px; letter-spacing: 2px; }
  .offer {
    position: absolute; left: 0; right: 0; top: 262px;
    text-align: center; color: var(--white);
    font-family: "Roboto Condensed", sans-serif; font-size: 19px; line-height: 1.3;
  }
  .back-rule {
    position: absolute; left: 70px; right: 70px; top: 322px;
    height: 1px; background: rgba(255,255,255,0.8);
  }
  .tagline {
    position: absolute; left: 0; right: 0; top: 336px;
    text-align: center; color: var(--white);
    font-family: "Roboto Condensed", sans-serif; font-size: 20px; letter-spacing: 0.5px;
  }
</style>
</head>
<body>
  <section class="card card-front">
    <h1 class="holder-name">NOLAN PIERCE</h1>
    <p class="holder-title">Story Marketing Coach</p>
    <div class="front-rule"></div>
    <ul class="contact-list">
      <li class="addr">QX2040, 8/3 Alder Row</li>
      <li class="addr">Fenmoor city, Westland</li>
      <li>
        <svg viewBox="0 0 16 16"><path fill="#f37122" d="M3.5 1.5l3 3-1.6 1.6c.9 2 2.2 3.4 4.1 4.2l1.6-1.6 3 3-1.9 1.9C6.5 13 3 9.5 1.6 3.4z"/></svg>
        (555) 014-2290
      </li>
      <li>
        <svg viewBox="0 0 16 16"><rect x="1.5" y="3.5" width="13" height="9" fill="none" stroke="#f37122" stroke-width="1.5"/><path d="M1.5 3.5L8 9l6.5-5.5" fill="none" stroke="#f37122" stroke-width="1.5"/></svg>
        Nolan@larkwellnow.com
      </li>
      <li>
        <svg viewBox="0 0 16 16"><circle cx="8" cy="8" r="6.5" fill="none" stroke="#f37122" stroke-width="1.5"/><path d="M1.5 8h13M8 1.5c-3 3.5-3 9.5 0 13M8 1.5c3 3.5 3 9.5 0 13" fill="none" stroke="#f37122" stroke-width="1.2"/></svg>
        <span>www.<span class="accent">larkwellnow</span>.com</span>
      </li>
    </ul>
    <div class="front-brand">
      <span class="brand-dot"></span>
      <span class="brand-name">LARKWELL</span>
    </div>
  </section>

  <section class="card card-back">
    <div class="map-pattern" role="img" aria-label="Faint dotted world map pattern across the card background"></div>
    <div class="back-brand">
      <span class="brand-dot"></span>
      <span class="brand-name">LARKWELL</span>
    </div>
    <p class="offer">Get your free Larkwell<br>Starter Package and our marketing guide today at</p>
    <div class="back-rule"></div>
    <p class="tagline">REACH MORE PEOPLE. MAKE MORE MONEY. CREATE MORE IMPACT.</p>
  </section>
</body>
</html>
```